Harlow Mechanical Contractors needs a Website

Create basic website for commercial plumbing and mechanical contractor; to include pictures of works in progress and completed works, description of all services offered and geographical locations and licenses

Target Market(s)

General Contractors, Real Estate Developers, Construction Companies

Industry/Entity Type

Construction

Coding

Coded - Design and coding required

Number of Pages Required

5+ page

• See logo attached to project

Colors
0392cd

```html
<!DOCTYPE html>
<html lang="en">
<head>
<meta charset="utf-8">
<title>Harlow Mechanical Contractors</title>
<link href="https://fonts.googleapis.com/css2?family=Raleway:wght@500;600;700;800&family=Open+Sans:wght@400;600;700&display=swap" rel="stylesheet">
<style>
:root{
  --brand:#0392cd;
  --brand-dark:#0a7fb8;
  --ink:#1d1d1d;
  --text:#333;
  --white:#fff;
  --bar:#3a3a3a;
  --btn-dark:#2f2f2f;
}
*{margin:0;padding:0;box-sizing:border-box}
html,body{width:674px;height:1200px;overflow:hidden;background:#fff}
body{position:relative;font-family:"Open Sans",sans-serif;color:var(--text)}
.abs{position:absolute}
.top-rule{left:0;top:0;width:674px;height:2px;background:var(--brand)}
.brand{display:flex;align-items:center;gap:6px}
.brand-dot{width:38px;height:38px;border-radius:50%;background:var(--brand);flex:none}
.brand-name{font-family:"Raleway",sans-serif;font-weight:800;font-size:8px;line-height:9px;text-transform:uppercase;color:#1b3a5c}
.site-header .brand{left:90px;top:13px}
.contact-chip{display:flex;align-items:center;gap:4px;font-size:7px;color:#444;top:14px}
.chip-icon{width:17px;height:17px;border:1.2px solid var(--brand);border-radius:50%;display:flex;align-items:center;justify-content:center}
.main-nav{top:45px;left:0;width:674px;height:10px}
.main-nav a{position:absolute;font-size:6.4px;color:#333;text-decoration:none;text-transform:uppercase;white-space:nowrap}
.main-nav a.active{color:var(--brand)}
.hero{left:0;top:69px;width:674px;height:269px}
.hero-copy{left:90px;top:146px;color:#fff}
.hero-title{font-family:"Raleway",sans-serif;font-weight:700;font-size:21px;letter-spacing:.5px;line-height:22px}
.hero-sub{font-family:"Raleway",sans-serif;font-weight:600;font-size:12.5px;margin-top:4px}
.hero-text{font-size:7.6px;line-height:12px;width:190px;margin-top:8px;color:#eee}
.hero-btn{left:90px;top:248px;width:114px;height:21px;border-radius:11px;background:var(--brand);color:#fff;font-family:"Raleway",sans-serif;font-weight:700;font-size:6.6px;display:flex;align-items:center;padding-left:15px}
.hero-btn span.end{position:absolute;right:0;top:0;width:22px;height:21px;border-radius:0 11px 11px 0;background:var(--brand-dark);display:flex;align-items:center;justify-content:center}
.slider-dots{left:92px;top:303px;display:flex;gap:2px}
.slider-dots i{width:8px;height:8px;border-radius:50%;background:#fff;display:block}
.slider-dots i.off{background:transparent;border:1.2px solid #fff}
.section-title{width:674px;left:0;text-align:center;font-family:"Raleway",sans-serif;font-weight:700;font-size:13px;color:var(--ink);letter-spacing:.2px}
.service{width:150px;text-align:center;top:406px}
.service svg{display:block;margin:0 auto}
.service h3{font-family:"Raleway",sans-serif;font-weight:600;font-size:9.4px;color:var(--ink);margin-top:14px;letter-spacing:.2px}
.service p{font-size:5.8px;line-height:10.5px;color:#444;margin-top:7px}
.service .more{display:block;font-family:"Raleway",sans-serif;font-weight:700;font-size:6px;color:var(--ink);margin-top:8px}
.connector{top:448px;height:1px;background:#e4e4e4}
.welcome{left:0;top:590px;width:674px;height:208px;background:var(--brand)}
.video{left:90px;top:623px;width:210px;height:144px}
.welcome-title{left:321px;top:626px;font-family:"Raleway",sans-serif;font-weight:700;font-size:12.4px;color:#fff;letter-spacing:.2px}
.welcome-text{left:322px;top:651px;width:262px;font-size:5.8px;line-height:11.4px;color:#e8f5fc;text-align:justify}
.btn-dark{background:var(--btn-dark);color:#fff;font-family:"Raleway",sans-serif;font-weight:700;font-size:6px;display:flex;align-items:center;justify-content:center}
.welcome-btn{left:322px;top:746px;width:53px;height:18px}
.post{top:846px;width:115px}
.post-img{width:115px;height:76px;display:block}
.post h4{font-family:"Open Sans",sans-serif;font-weight:400;font-size:8.6px;color:#333;margin-top:5px;white-space:nowrap}
.post-meta{display:flex;gap:9px;font-size:5.6px;color:var(--brand);font-weight:600;margin-top:7px}
.post p{font-size:5.6px;line-height:10.6px;color:#333;margin-top:5px}
.footer-bg{left:0;top:1008px;width:674px;height:154px}
.site-footer .brand{left:90px;top:1058px}
.site-footer .brand-dot{background:#fff}
.site-footer .brand-name{color:#fff}
.social{left:90px;top:1113px;display:flex;gap:3px}
.social i{width:15px;height:15px;border:1px solid #fff;border-radius:50%;display:block}
.col-rule{top:1062px;width:1px;height:80px;background:rgba(255,255,255,.25)}
.foot-col h5{font-family:"Raleway",sans-serif;font-weight:600;font-size:9px;color:#fff;letter-spacing:.2px}
.foot-list{list-style:none;margin-top:6px}
.foot-list li{font-size:6.2px;color:#fff;line-height:12.6px;display:flex;align-items:flex-start;gap:5px}
.foot-list.contact li{line-height:11.4px}
.foot-list svg{flex:none;margin-top:3px}
.newsletter p{font-size:6.2px;color:#fff;margin-top:3px}
.email-field{margin-top:7px;width:136px;height:19px;background:#fff;font-size:5.6px;font-style:italic;color:#888;padding-left:7px;display:flex;align-items:center}
.newsletter .btn-dark{width:48px;height:17px;margin-top:6px;font-size:6.2px}
.bottom-bar{left:0;top:1162px;width:674px;height:38px;background:var(--bar);color:#ddd;font-size:5.6px;display:flex;align-items:center;justify-content:center}
</style>
</head>
<body>
<div class="abs top-rule"></div>

<header class="site-header">
  <div class="abs brand">
    <span class="brand-dot"></span>
    <span class="brand-name">Harlow<br>Mechanical<br>Contractors</span>
  </div>
  <div class="abs contact-chip" style="left:377px">
    <span class="chip-icon"><svg width="8" height="8" viewBox="0 0 10 10"><path d="M2.2 1.2c.4-.3.9-.2 1.1.2l.8 1.4c.2.4.1.8-.2 1l-.6.4c.4.9 1.3 1.8 2.2 2.2l.4-.6c.3-.3.7-.4 1-.2l1.4.8c.4.2.5.7.2 1.1-.6.9-1.6 1.1-2.6.6C4 7.3 2.7 6 1.9 4.2c-.5-1-.2-2.3.3-3z" fill="#0392cd"/></svg></span>
    Call:555-014-2200
  </div>
  <div class="abs contact-chip" style="left:470px">
    <span class="chip-icon"><svg width="8" height="7" viewBox="0 0 10 8"><rect x=".5" y=".5" width="9" height="7" fill="none" stroke="#0392cd"/><path d="M.5 .8 5 4.5 9.5.8" fill="none" stroke="#0392cd"/></svg></span>
    info@harlowmech.example
  </div>
  <nav class="abs main-nav">
    <a class="active" style="left:252px">Home</a>
    <a style="left:291px">Our Services</a>
    <a style="left:358px">Products</a>
    <a style="left:412px">Solutions</a>
    <a style="left:468px">Success Stories</a>
    <a style="left:543px">Contact Us</a>
  </nav>
</header>

<section class="abs hero">
  <svg width="674" height="269" viewBox="0 0 674 269">
    <defs>
      <linearGradient id="woodTone" x1="0" y1="0" x2="1" y2="1">
        <stop offset="0" stop-color="#6b6e70"/><stop offset=".6" stop-color="#4e5153"/><stop offset="1" stop-color="#3e4143"/>
      </linearGradient>
      <linearGradient id="toolsTone" x1="0" y1="0" x2="1" y2="1">
        <stop offset="0" stop-color="#6d6e6c"/><stop offset=".5" stop-color="#a58a64"/><stop offset="1" stop-color="#5a4a3c"/>
      </linearGradient>
    </defs>
    <rect width="674" height="269" fill="url(#woodTone)" role="img" aria-label="Dark weathered wooden board background"/>
    <path d="M290 0 C262 50 262 95 292 150 C318 200 312 240 300 269 L674 269 L674 0 Z" fill="url(#toolsTone)" role="img" aria-label="Brass pipe fittings, a leather work glove and a red pipe wrench on wood"/>
    <path d="M290 0 C262 50 262 95 292 150 C318 200 312 240 300 269" fill="none" stroke="#fff" stroke-width="4"/>
  </svg>
</section>
<div class="abs hero-copy">
  <div class="hero-title">HARLOW</div>
  <div class="hero-sub">MECHANICAL CONTRACTOR</div>
  <p class="hero-text">Sed ut perspiciatis unde omnis iste natussit volup tatem accus an tium doloremqueaudantium, totam rem aperiam, eaque ipsuae.</p>
</div>
<div class="abs hero-btn">GET STARTED HERE<span class="end"><svg width="7" height="7" viewBox="0 0 8 8"><circle cx="4" cy="4" r="3.2" fill="none" stroke="#fff"/><circle cx="4" cy="4" r="1.2" fill="#fff"/></svg></span></div>
<div class="abs slider-dots"><i></i><i class="off"></i><i></i><i></i></div>

<h2 class="abs section-title" style="top:357px">PLUMBING SERVICES</h2>
<div class="abs connector" style="left:200px;width:94px"></div>
<div class="abs connector" style="left:379px;width:94px"></div>

<div class="abs service" style="left:83px">
  <svg width="84" height="84" viewBox="0 0 84 84"><circle cx="42" cy="42" r="40" fill="var(--brand)"/><circle cx="42" cy="42" r="29" fill="#fff"/><circle cx="42" cy="42" r="25" fill="none" stroke="var(--brand)" stroke-width="1"/><rect x="32" y="31" width="11" height="22" fill="#222"/><rect x="43" y="39" width="10" height="14" fill="#222"/><g fill="#fff"><rect x="34" y="34" width="2" height="2"/><rect x="38" y="34" width="2" height="2"/><rect x="34" y="39" width="2" height="2"/><rect x="38" y="39" width="2" height="2"/><rect x="34" y="44" width="2" height="2"/><rect x="38" y="44" width="2" height="2"/><rect x="45" y="42" width="2" height="2"/><rect x="49" y="42" width="2" height="2"/><rect x="45" y="47" width="2" height="2"/><rect x="49" y="47" width="2" height="2"/></g></svg>
  <h3>LARGE OFFICES</h3>
  <p>Sed ut perspiciatis unde omstusit voluptatema nti loum dolore au dantium, totam rem aperiadut erspiciatis unde omstusit voluptatem accu.</p>
  <span class="more">READ MORE</span>
</div>
<div class="abs service" style="left:262px">
  <svg width="84" height="84" viewBox="0 0 84 84"><circle cx="42" cy="42" r="40" fill="var(--brand)"/><circle cx="42" cy="42" r="29" fill="#fff"/><circle cx="42" cy="42" r="25" fill="none" stroke="var(--brand)" stroke-width="1"/><path d="M35 54V33l7-4 7 4v21z" fill="#222"/><g fill="#fff"><rect x="38" y="36" width="2" height="2"/><rect x="44" y="36" width="2" height="2"/><rect x="38" y="41" width="2" height="2"/><rect x="44" y="41" width="2" height="2"/><rect x="38" y="46" width="2" height="2"/><rect x="44" y="46" width="2" height="2"/></g></svg>
  <h3>CONDOMINIUMS</h3>
  <p>Sed ut perspiciatis unde omstusit voluptatema nti loum dolore au dantium, totam rem aperiadut erspiciatis unde omstusit voluptatem accu.</p>
  <span class="more">READ MORE</span>
</div>
<div class="abs service" style="left:440px">
  <svg width="84" height="84" viewBox="0 0 84 84"><circle cx="42" cy="42" r="40" fill="var(--brand)"/><circle cx="42" cy="42" r="29" fill="#fff"/><circle cx="42" cy="42" r="25" fill="none" stroke="var(--brand)" stroke-width="1"/><path d="M30 53V42l6-4v4l6-4v4l6-4V32h3v21z" fill="#222"/><g fill="#fff"><rect x="33" y="46" width="2" height="2"/><rect x="39" y="46" width="2" height="2"/><rect x="45" y="46" width="2" height="2"/></g></svg>
  <h3>INDUSTRIAL PROJECTS</h3>
  <p>Sed ut perspiciatis unde omstusit voluptatema nti loum dolore au dantium, totam rem aperiadut erspiciatis unde omstusit voluptatem accu.</p>
  <span class="more">READ MORE</span>
</div>

<section class="abs welcome"></section>
<svg class="abs video" viewBox="0 0 210 144">
  <defs><linearGradient id="videoTone" x1="0" y1="0" x2="1" y2="1"><stop offset="0" stop-color="#5a3b30"/><stop offset=".5" stop-color="#a89a86"/><stop offset="1" stop-color="#3b2a24"/></linearGradient></defs>
  <rect width="210" height="144" fill="url(#videoTone)" role="img" aria-label="Video still of hands tightening a brass fitting with an adjustable wrench"/>
  <circle cx="105" cy="72" r="13" fill="#fff"/><circle cx="105" cy="72" r="11" fill="#e02424"/><path d="M101 66v12l10-6z" fill="#fff"/>
</svg>
<h2 class="abs welcome-title">WELCOME TO MECHANICAL CONTRACTOR</h2>
<p class="abs welcome-text">Sed ut perspiciatis unde omnis iste natus error sit voluptatem accusantium doloremque laudantium, totam rem aperiam, eaque ipsa quae ab illo inventore veritatis et quasi architecto beatae vitae dicta sunt explicabo. Nemo enim ipsam voluptatem quia voluptas sit aspernatur aut odit aut fugit, sed quia consequuntur magni dolores eos qui rabeatae vitae dicta sunt explicabo. Nemo enim ipsam voluptatem quia voluptas sit aspernatur aut odit aut fugit, sed quia consequuntur magni dolores eos quitione voluptatem sequi nesciunsed quia consequuntur magni dolores eos qui rabeatae vitae dicta sunt explicabvoluptatem sequi nesciuntcons equuntu r magni dolores eos quitione voluptatem</p>
<div class="abs btn-dark welcome-btn">READ MORE</div>

<h2 class="abs section-title" style="top:817px">LATETS BLOG NEWS</h2>

<article class="abs post" style="left:90px">
  <svg class="post-img" viewBox="0 0 115 76" role="img" aria-label="Plumber fitting pipes under a sink"><rect width="115" height="76" fill="#b9b3ad"/><rect y="40" width="115" height="36" fill="#8f8780"/></svg>
  <h4>Sed ut perspiciatis de omn</h4>
  <div class="post-meta"><span>▢July 11,2016</span><span>● Admin</span></div>
  <p>Sed ut perspiciatis unde omnis isa tusr orsit voluptatem accusa ntiu mdoloreu elaudantiumed ut perspiciatis.</p>
</article>
<article class="abs post" style="left:217px">
  <svg class="post-img" viewBox="0 0 115 76" role="img" aria-label="Brass fittings and a red wrench on a workbench"><rect width="115" height="76" fill="#a68c6a"/><rect x="60" y="30" width="55" height="46" fill="#b3503a"/></svg>
  <h4>Sed ut perspiciatis de omn</h4>
  <div class="post-meta"><span>▢July 11,2016</span><span>● Admin</span></div>
  <p>Sed ut perspiciatis unde omnis isa tusr orsit voluptatem accusa ntiu mdoloreu elaudantiumed ut perspiciatis.</p>
</article>
<article class="abs post" style="left:343px">
  <svg class="post-img" viewBox="0 0 115 76" role="img" aria-label="Plumber working on an overhead pipe"><rect width="115" height="76" fill="#d9d5cf"/><rect x="40" y="20" width="50" height="56" fill="#8a8178"/></svg>
  <h4>Sed ut perspiciatis de omn</h4>
  <div class="post-meta"><span>▢July 11,2016</span><span>● Admin</span></div>
  <p>Sed ut perspiciatis unde omnis isa tusr orsit voluptatem accusa ntiu mdoloreu elaudantiumed ut perspiciatis.</p>
</article>
<article class="abs post" style="left:469px">
  <svg class="post-img" viewBox="0 0 115 76" role="img" aria-label="Technician in blue overalls beside a boiler"><rect width="115" height="76" fill="#cfd3d6"/><rect x="30" y="25" width="50" height="51" fill="#24426e"/></svg>
  <h4>Sed ut perspiciatis de omn</h4>
  <div class="post-meta"><span>▢July 11,2016</span><span>● Admin</span></div>
  <p>Sed ut perspiciatis unde omnis isa tusr orsit voluptatem accusa ntiu mdoloreu elaudantiumed ut perspiciatis.</p>
</article>

<footer class="site-footer">
  <svg class="abs footer-bg" viewBox="0 0 674 154" preserveAspectRatio="none">
    <path d="M0 20 C120 -4 200 2 330 18 C460 34 560 30 674 6 L674 154 L0 154 Z" fill="var(--brand)"/>
  </svg>
  <div class="abs brand">
    <span class="brand-dot"></span>
    <span class="brand-name">Harlow<br>Mechanical<br>Contractors</span>
  </div>
  <div class="abs social"><i></i><i></i><i></i><i></i><i></i></div>
  <div class="abs col-rule" style="left:210px"></div>
  <div class="abs col-rule" style="left:292px"></div>
  <div class="abs col-rule" style="left:418px"></div>
  <div class="abs foot-col" style="left:226px;top:1061px">
    <h5>LINKS</h5>
    <ul class="foot-list"><li>Home</li><li>About us</li><li>Services</li><li>News</li><li>Contact Us</li></ul>
  </div>
  <div class="abs foot-col" style="left:310px;top:1061px">
    <h5>CONTACT US</h5>
    <ul class="foot-list contact">
      <li><svg width="5" height="6" viewBox="0 0 10 12"><path d="M5 0a4 4 0 0 1 4 4c0 3-4 8-4 8S1 7 1 4a4 4 0 0 1 4-4z" fill="#fff"/></svg><span>Postal address: PO Box 218,<br>Linden Vale Road North</span></li>
      <li><svg width="6" height="6" viewBox="0 0 10 10"><path d="M2 1c.4-.3.9-.2 1.1.2l.8 1.4c.2.4.1.8-.2 1l-.6.4c.4.9 1.3 1.8 2.2 2.2l.4-.6c.3-.3.7-.4 1-.2l1.4.8c.4.2.5.7.2 1.1-.6.9-1.6 1.1-2.6.6C4 7.3 2.7 6 1.9 4.2 1.4 3.2 1.5 1.9 2 1z" fill="#fff"/></svg>Phone: 555-017-4410</li>
      <li><svg width="6" height="6" viewBox="0 0 10 10"><rect x="1" y="3" width="8" height="5" fill="#fff"/><rect x="3" y="1" width="4" height="2" fill="#fff"/></svg>Fax: 555-017-4411</li>
      <li><svg width="6" height="5" viewBox="0 0 10 8"><rect width="10" height="8" fill="#fff"/><path d="M0 0 5 4 10 0" fill="none" stroke="#0392cd"/></svg>office@harlowmech.example</li>
    </ul>
  </div>
  <div class="abs foot-col newsletter" style="left:447px;top:1061px">
    <h5>SIGN UP NEWSLETTER</h5>
    <p>Please sign up here for latest deals</p>
    <div class="email-field">Email address</div>
    <div class="btn-dark">SIGN UP</div>
  </div>
  <div class="abs bottom-bar">© 2016 All Copyrights are reserved &nbsp;Term of Use. Privacy Policy</div>
</footer>
</body>
</html>
```